Brightmill Data Works

Our company is about IT hardwares and IT solutions. IT hardware such as PC, RAMS, storage and servers. IT solutions such as project management, BA. We are also selling new technology too.

Target Market(s)

Consumer, Small to Medium Business, Corporate

Requirements
Must have
• The business card must have the following:
• Name:
• Title:
• Contact Number:
• Email address:
• Website:
• Color: Must match the logo color upgrade

```html
<!DOCTYPE html>
<html lang="en">
<head>
<meta charset="UTF-8">
<title>Brightmill Data Works – Business Card</title>
<link rel="stylesheet" href="https://fonts.googleapis.com/css2?family=Open+Sans:wght@400;600;800&display=swap">
<style>
  :root {
    --bg: #2b2b2b;
    --orange: #c4672a;
    --orange-light: #d98a3c;
    --black: #121212;
    --white: #ffffff;
    --rule: rgba(255,255,255,0.75);
  }
  * { box-sizing: border-box; margin: 0; padding: 0; }
  html, body { width: 1200px; height: 896px; overflow: hidden; }
  body {
    background: var(--bg);
    font-family: "Open Sans", Arial, sans-serif;
    display: flex; flex-direction: column; align-items: center; justify-content: center;
    gap: 40px;
  }
  .card {
    width: 680px; height: 388px; position: relative;
    box-shadow: 0 10px 30px rgba(0,0,0,0.45);
    overflow: hidden;
  }
  .wordmark {
    font-family: "Open Sans", Arial, sans-serif;
    font-weight: 800; color: var(--white);
    text-transform: uppercase; line-height: 1.05;
  }

  /* Front */
  .card--front { background: var(--orange); }
  .card--front .wordmark {
    position: absolute; left: 120px; top: 118px;
    font-size: 52px; letter-spacing: 2px;
  }
  .card--front .tagline {
    position: absolute; left: 122px; top: 250px;
    color: var(--white); font-size: 15px; letter-spacing: 0.5px;
    text-transform: uppercase;
  }

  /* Back */
  .card--back { background: var(--black); }
  .person { position: absolute; left: 48px; top: 62px; }
  .person__name {
    color: var(--orange-light); font-weight: 600; font-size: 22px;
    text-transform: uppercase; letter-spacing: 1px;
  }
  .person__title { color: var(--white); font-size: 17px; margin-top: -2px; }
  .person__rule {
    position: absolute; left: 200px; top: 125px; width: 432px; height: 1px;
    background: var(--rule);
  }
  .brand {
    position: absolute; right: 48px; top: 150px;
    display: flex; align-items: center; gap: 16px;
  }
  .brand__dot { width: 34px; height: 34px; border-radius: 50%; background: var(--orange-light); }
  .card--back .wordmark { font-size: 34px; letter-spacing: 1px; }
  .contact__rule {
    position: absolute; right: 48px; top: 262px; width: 300px; height: 1px;
    background: var(--rule);
  }
  .contact {
    position: absolute; right: 48px; top: 274px;
    list-style: none; text-align: right;
  }
  .contact li {
    color: var(--white); font-size: 16px; line-height: 24px;
    display: flex; justify-content: flex-end; align-items: center; gap: 10px;
  }
  .contact svg { width: 14px; height: 14px; fill: var(--orange-light); }
</style>
</head>
<body>
  <section class="card card--front">
    <div class="wordmark">Brightmill<br>Data Works</div>
    <p class="tagline">IT Hardwares and IT Solutions</p>
  </section>

  <section class="card card--back">
    <div class="person">
      <p class="person__name">Marcus Ellery</p>
      <p class="person__title">Managing Director</p>
    </div>
    <div class="person__rule"></div>

    <div class="brand">
      <span class="brand__dot"></span>
      <div class="wordmark">Brightmill<br>Data Works</div>
    </div>

    <div class="contact__rule"></div>
    <ul class="contact">
      <li>044-555 018 240
        <svg viewBox="0 0 24 24" aria-hidden="true"><path d="M6.6 10.8a15.1 15.1 0 0 0 6.6 6.6l2.2-2.2c.3-.3.7-.4 1-.2 1.1.4 2.3.6 3.6.6.6 0 1 .4 1 1V20c0 .6-.4 1-1 1A17 17 0 0 1 3 4c0-.6.4-1 1-1h3.5c.6 0 1 .4 1 1 0 1.3.2 2.5.6 3.6.1.3 0 .7-.2 1z"/></svg>
      </li>
      <li>info@brightmilldata.com
        <svg viewBox="0 0 24 24" aria-hidden="true"><path d="M2 5h20v14H2zm2 2v.5l8 5 8-5V7l-8 5z"/></svg>
      </li>
      <li>www.brightmilldata.com
        <svg viewBox="0 0 24 24" aria-hidden="true"><path d="M12 2a10 10 0 1 0 0 20 10 10 0 0 0 0-20zm6.9 6h-3a15 15 0 0 0-1.3-3.9A8 8 0 0 1 18.9 8zM12 4c.8 1.2 1.5 2.5 1.9 4h-3.8c.4-1.5 1.1-2.8 1.9-4zM4.3 14a8 8 0 0 1 0-4h3.4a16 16 0 0 0 0 4zm.8 2h3a15 15 0 0 0 1.3 3.9A8 8 0 0 1 5.1 16zm3-8h-3a8 8 0 0 1 4.3-3.9C8.8 5.3 8.4 6.6 8.1 8zM12 20c-.8-1.2-1.5-2.5-1.9-4h3.8c-.4 1.5-1.1 2.8-1.9 4zm2.3-6H9.7a14 14 0 0 1 0-4h4.6a14 14 0 0 1 0 4zm.3 5.9c.6-1.2 1-2.5 1.3-3.9h3a8 8 0 0 1-4.3 3.9zm1.7-5.9a16 16 0 0 0 0-4h3.4a8 8 0 0 1 0 4z"/></svg>
      </li>
    </ul>
  </section>
</body>
</html>
```